Lucky Harbour Fun Casino Entertainment

Looking to update my business card and make it look more modern, stand out and eye catching.
We are are fun casino business in Australia (primarily Sydney). Blackjack and Roulette are our most popular games although we have pretty much every game available for hire that you would find in a real casino. The final design would need to be sleek and appeal to the more upmarket corporate sector.
We mainly cater for Corporate Events, Private Parties, Fundraising Events, Team Building, Poker Tournaments
I think I'd prefer the colour Black.

Target Market(s)

High-end Corporate

Industry/Entity Type

Events

Contact Information for Business Card

Rob Kendall
Director
1300 482 617
0433 728 591
info@luckyharbour.com.au
www.luckyharbour.com.au
Facebook & Instagram @luckyharbourevents (proper social icons preferred)

Colors
000000
0255a3

Requirements
Must have
• Front side:
• Logo
• Contact details
• 'Sydney's Premier Fun Casino Entertainers'
• Back:
• Logo
Nice to have
• Back:
• Corporate Events
• Private Parties
• Poker Tournaments
• Fundraising
• Props & Theming
• Photo Booth
• Horse Racing Events
• The Vegas Sign attached, maybe on the back of the card in the background...?

```html
<!DOCTYPE html>
<html lang="en">
<head>
<meta charset="utf-8">
<title>Lucky Harbour – Business Card</title>
<link href="https://fonts.googleapis.com/css2?family=Open+Sans:wght@300;400;600;700&display=swap" rel="stylesheet">
<style>
  :root {
    --page: #1e2226;
    --card: #2e2e2e;
    --card-edge: #262626;
    --orange: #f7a21b;
    --gold: #f2c230;
    --white: #f2f2f2;
    --grey: #c9c9c9;
  }
  * { box-sizing: border-box; margin: 0; padding: 0; }
  html, body { width: 1200px; height: 900px; overflow: hidden; }
  body {
    background: var(--page);
    font-family: "Open Sans", Arial, sans-serif;
    display: flex; flex-direction: column; align-items: center; justify-content: center; gap: 48px;
  }
  .card {
    position: relative; width: 640px; height: 366px; border-radius: 22px;
    background: linear-gradient(160deg, #353535 0%, var(--card) 55%, var(--card-edge) 100%);
    box-shadow: 0 14px 30px rgba(0,0,0,.45);
    overflow: hidden;
  }
  .brand { display: flex; align-items: center; gap: 10px; }
  .brand-dot { width: 38px; height: 38px; border-radius: 50%; background: var(--orange); flex: none; }
  .brand-name { color: var(--orange); font-weight: 700; font-size: 28px; letter-spacing: .5px; white-space: nowrap; }
  .tagline { color: var(--white); font-weight: 600; font-size: 14px; white-space: nowrap; }

  /* Front */
  .front .brand-area { position: absolute; left: 38px; top: 120px; width: 280px; }
  .front .tagline { margin-top: 16px; }
  .front .divider { position: absolute; left: 0; top: 0; }
  .contact { position: absolute; left: 360px; top: 70px; }
  .person-name { color: var(--orange); font-weight: 700; font-size: 28px; line-height: 1.1; }
  .person-role { color: var(--grey); font-weight: 300; font-size: 15px; margin-bottom: 12px; }
  .address { display: flex; gap: 8px; color: var(--orange); font-weight: 700; font-size: 14px; line-height: 1.35; margin-bottom: 10px; }
  .row { display: flex; align-items: center; gap: 8px; color: var(--white); font-size: 13.5px; line-height: 1.75; }
  .row .sep { margin-left: 6px; }
  .icon { width: 14px; height: 14px; flex: none; }
  .address .icon { margin-top: 2px; }
  .social-dot { border-radius: 50%; background: var(--orange); }

  /* Back */
  .back .accent { position: absolute; height: 3px; }
  .back .accent.top { left: 70px; top: 44px; width: 130px; background: linear-gradient(90deg, transparent, var(--gold), var(--orange)); }
  .back .accent.side { right: 0; top: 150px; width: 100px; background: linear-gradient(90deg, transparent, var(--gold), var(--orange)); }
  .back .center { position: absolute; left: 0; right: 0; top: 90px; display: flex; flex-direction: column; align-items: center; }
  .back .tagline { margin-top: 18px; font-size: 16px; font-weight: 700; }
  .back .rule { width: 230px; height: 1px; margin-top: 10px; background: linear-gradient(90deg, transparent, var(--gold), transparent); }
  .services { margin-top: 20px; color: var(--orange); font-weight: 300; font-size: 15px; text-align: center; line-height: 1.7; }
  .services .bullet { display: inline-block; width: 7px; height: 7px; border: 1px solid var(--orange); border-radius: 50%; margin: 0 7px 2px; vertical-align: middle; }
</style>
</head>
<body>

<section class="card front" aria-label="Business card front">
  <svg class="divider" width="640" height="366" viewBox="0 0 640 366" aria-hidden="true">
    <defs>
      <linearGradient id="goldLine" x1="0" y1="1" x2="1" y2="0">
        <stop offset="0" stop-color="#f2c230" stop-opacity="0"/>
        <stop offset=".5" stop-color="#f2c230"/>
        <stop offset="1" stop-color="#f7a21b" stop-opacity=".2"/>
      </linearGradient>
    </defs>
    <line x1="305" y1="320" x2="345" y2="80" stroke="url(#goldLine)" stroke-width="2"/>
  </svg>

  <div class="brand-area">
    <div class="brand"><span class="brand-dot"></span><span class="brand-name">Lucky Harbour</span></div>
    <p class="tagline">Sydney's Premier Fun Casino Entertainers</p>
  </div>

  <div class="contact">
    <h1 class="person-name">Rob Kendall</h1>
    <p class="person-role">Director</p>
    <p class="address">
      <svg class="icon" viewBox="0 0 14 14" aria-hidden="true"><circle cx="7" cy="7" r="6.3" fill="none" stroke="#f7a21b"/><path d="M7 3.2a2.4 2.4 0 0 0-2.4 2.4C4.6 7.4 7 10.6 7 10.6s2.4-3.2 2.4-5A2.4 2.4 0 0 0 7 3.2z" fill="#f7a21b"/></svg>
      <span>5/218 Harbour Street,<br>Rosebery 2018</span>
    </p>
    <p class="row">
      <svg class="icon" viewBox="0 0 14 14" aria-hidden="true"><circle cx="7" cy="7" r="6.3" fill="none" stroke="#f7a21b"/><path d="M4.6 3.8l1.4-.4.8 1.7-.9.7c.4.9 1 1.5 1.9 1.9l.7-.9 1.7.8-.4 1.4c-2.9.2-5.4-2.3-5.2-5.2z" fill="#f7a21b"/></svg>
      1300 482 617
      <svg class="icon sep" viewBox="0 0 14 14" aria-hidden="true"><circle cx="7" cy="7" r="6.3" fill="none" stroke="#f7a21b"/><rect x="5" y="3.3" width="4" height="7.4" rx=".8" fill="#f7a21b"/></svg>
      0433 728 591
    </p>
    <p class="row">
      <svg class="icon" viewBox="0 0 14 14" aria-hidden="true"><circle cx="7" cy="7" r="6.3" fill="none" stroke="#f7a21b"/><rect x="3.6" y="4.6" width="6.8" height="4.8" fill="#f7a21b"/><path d="M3.6 4.6L7 7.3l3.4-2.7" fill="none" stroke="#2e2e2e" stroke-width=".8"/></svg>
      info@luckyharbour.com.au
    </p>
    <p class="row">
      <svg class="icon" viewBox="0 0 14 14" aria-hidden="true"><circle cx="7" cy="7" r="6.3" fill="none" stroke="#f7a21b"/><circle cx="7" cy="7" r="3.6" fill="none" stroke="#f7a21b"/><path d="M3.4 7h7.2M7 3.4c-1.6 2.2-1.6 5 0 7.2M7 3.4c1.6 2.2 1.6 5 0 7.2" fill="none" stroke="#f7a21b" stroke-width=".7"/></svg>
      www.luckyharbour.com.au
    </p>
    <p class="row"><span class="icon social-dot"></span>@luckyharbourevents</p>
    <p class="row"><span class="icon social-dot"></span>@luckyharbourevents</p>
  </div>
</section>

<section class="card back" aria-label="Business card back">
  <span class="accent top"></span>
  <span class="accent side"></span>
  <div class="center">
    <div class="brand"><span class="brand-dot"></span><span class="brand-name">Lucky Harbour</span></div>
    <p class="tagline">Sydney's Premier Fun Casino Entertainers</p>
    <span class="rule"></span>
    <p class="services">
      <span class="bullet"></span>Corporate Events<span class="bullet"></span>Private Parties<span class="bullet"></span>Poker Tournaments<br>
      <span class="bullet"></span>Fundraising<span class="bullet"></span>Props &amp; Theming<span class="bullet"></span>Photo Booth<span class="bullet"></span>Horse Racing Events
    </p>
  </div>
</section>

</body>
</html>
```